San Francisco Leading Consulting firm - 47Vora Web Design Project

•Create a Web Design
•Uncoded webpage layout design
•2 Pages Design - Homepage + Interior Page

Task Description
Hello, we're looking for a re-design our current website www.47vora-example.com

we have a sample mockup design @

http://47vora.pubtrellis-example.org/

This shows the layout that we like and also a sample of 6 pictures that would change based on where you mouse over..

6 pictures HOME design needs to be included.

SMART
THOUGHTFUL
FLEXIBLE
CREATIVE SERVICES
TECHNICAL SERVICES
PARTNERS

sites we like:

http://www.melvanadvisory-example.com/Home.cfm?id=Home
http://www.plinthworks-example.com/index.html

Our company can be best described as: 100+ employees, cutting-edge, depandable, innovative, strong, smart.

Our Primary focus is: IT Consulting Services and Creative Design services

47Vora LLC is a consulting firm providing creative design, business and technology solutions to both private and public interests.

Established in 1996, 47Vora is a San Francisco based company providing specialists for a range of business needs including:

Creative Design Services
•Print
•Logo Design
•Website Design
•Illustration

and

Business and Technology solutions

•Application Software and Web Development
•Business Process Re-Design (BPR)
•Business/Systems Analysis and Requirement Documentation
•Mentoring and Training
•Network/Hardware Installation Services
•System Design and Architecture
•Vendor Management
•Docuvault Architecture and Implementation

our sample mockup site:

Reason: Due to holiday season, we're not available to work with designers and finilize our design.  

Thank you very much for submitting your design.

We appreciate your time and creativity.   Since, our office is currently closed for holidays, we will be reviewing it in details next week and will make our decision as soon as possible.

It would be great if you could submit any of your changes by Wed next week, so it would be part of our reviews. 

Please see updated wireframe under attachments:  we have some minor updates to our wireframe that we would like you to update your designs, if possible.  

We also encorouge you not to use our standard wireframe and come up with more unique designs.   Everything would be considered when we review your design.

 

Target Market(s)

Creative services and professional services clients, including government agencies

Industry/Entity Type

Business

Requirements
Must have
• Clean, professional look, easy navigation

```html
<!DOCTYPE html>
<html lang="en">
<head>
<meta charset="utf-8">
<title>47Vora – Home</title>
<link rel="stylesheet" href="https://fonts.googleapis.com/css2?family=Arimo:wght@400;700&display=swap">
<style>
:root{
  --ink:#1a1a1a;
  --text:#333;
  --accent:#1b3fe0;
  --dark:#0c0e0f;
  --nav:#1b1d1e;
  --panel:#121516;
  --blue-top:#3fa8f0;
  --blue-bot:#1f7fe6;
  --rule:#d4d8da;
  --muted:#c8c8c8;
}
*{box-sizing:border-box;margin:0;padding:0}
html,body{width:1118px;height:1200px;overflow:hidden;background:#fff;font-family:"Arimo",Arial,sans-serif;color:var(--text)}
.page{position:relative;width:1118px;height:1200px}
.abs{position:absolute}

.header{left:90px;top:0;width:938px;height:126px;background:linear-gradient(180deg,#e4e4e4 0%,#c8c8c8 100%)}
.brand{left:84px;top:46px;font-size:38px;letter-spacing:2px;color:#2b2b2b;font-weight:400}
.brand-mark{left:18px;top:18px;width:38px;height:38px;border-radius:50%;background:#2a9fe0}
.nav{left:349px;top:89px;width:589px;height:37px;background:var(--nav);display:flex;align-items:center;padding-left:24px;color:#fff;font-size:13px}
.nav span{white-space:nowrap}
.nav .sep{margin:0 19px}

.hero{left:90px;top:126px;width:938px;height:361px;background:var(--dark)}
.hero-photo{left:12px;top:10px;width:650px;height:340px;background:linear-gradient(135deg,#b7a088 0%,#d8c6a4 40%,#a9b86a 60%,#b88a66 100%)}
.slide-box{left:672px;top:10px;width:254px;height:274px;background:var(--panel);border:1px solid #222}
.slide-title{left:15px;top:19px;width:233px;height:30px;background:linear-gradient(90deg,#2b2e30,#151819);color:#fff;font-size:19px;padding:5px 9px}
.slide-text{left:19px;top:64px;width:218px;font-size:11.3px;line-height:18.6px;color:#eee;text-align:justify}
.readmore{left:167px;top:239px;width:74px;height:23px;background:#2d3133;color:#ddd;font-size:12px;text-align:center;line-height:23px}
.slide-nav{left:672px;top:295px;width:255px;height:52px;background:linear-gradient(90deg,#2b3033,#1b1f21 40%,#30363a);border:1px solid #333}

.content{left:90px;top:487px;width:938px;height:489px;background:linear-gradient(#e6ecef,#fff 60%)}
.h2{font-size:15.5px;color:var(--ink);font-weight:400}
.h2 em{font-style:normal;color:var(--accent)}
.rule{height:1px;background:var(--rule)}
.client-logo{left:115px;top:553px;width:264px;height:160px;background:#fff;border:1px solid #ddd}
.client-name{left:0;top:64px;width:100%;text-align:center;font-size:22px;color:#3a3f7a}
.para{font-size:11.2px;line-height:16.8px;color:var(--text);text-align:justify}
.btn{height:21px;background:#0a0a0a;color:#fff;font-size:11.5px;line-height:21px;text-align:center;border-radius:3px}
.services{left:424px;top:550px;width:265px;list-style:none}
.services li{position:relative;padding-left:11px;font-size:11.2px;line-height:18.6px;color:#222;margin-bottom:10.3px}
.services li span{border-bottom:1px dotted #777;display:inline-block;padding-bottom:1px}
.services li::before{content:"";position:absolute;left:1px;top:7px;border-left:3px solid #333;border-top:2.5px solid transparent;border-bottom:2.5px solid transparent}
.services li.active{color:var(--accent)}
.partner-photo{left:729px;top:555px;width:99px;height:99px;border:2px solid #8ee0f0;background:linear-gradient(135deg,#cfe9f0,#d9a58a 50%,#c98a6c)}

.tiles{left:113px;top:872px;width:885px;height:144px;border:1px solid #1a63c9;border-radius:4px;background:linear-gradient(var(--blue-top),var(--blue-bot));display:flex;overflow:hidden}
.tile{position:relative;border-right:1px solid #d8ecff;height:100%}
.tile:last-child{border-right:0}
.tile h3{font-weight:400;color:#fff;font-size:16.5px;text-align:center;margin-top:9px}
.tile .line{position:absolute;left:6px;right:13px;top:36px;height:1px;background:#d8f0ff}
.tile .art{position:absolute;left:50%;top:50px;width:68px;height:68px;margin-left:-34px;border-radius:8px;background:linear-gradient(135deg,rgba(255,255,255,.35),rgba(255,255,255,.1))}
.more{position:absolute;bottom:4px;height:17px;display:flex;background:#fff;border-radius:2px;font-size:10.5px;color:#1a5fc6;line-height:17px}
.more span{padding:0 5px}
.more b{border-left:1px solid #aac;padding:0 5px;font-weight:700}

.footer{left:90px;top:976px;width:938px;height:224px;background:var(--dark)}
.fcol h4{font-weight:400;font-size:11.5px;color:#fff;padding-bottom:8px;border-bottom:1px dotted #444;width:140px}
.fcol ul{list-style:none;margin-top:12px}
.fcol li{font-size:10.3px;color:var(--muted);line-height:22.4px;white-space:nowrap}
.fcol.arrows li::before{content:"» ";color:#888}
.ico{display:inline-block;width:12px;height:12px;background:#3a78c8;border-radius:2px;vertical-align:-2px;margin-right:7px}
.flogo{left:876px;top:1096px;font-size:24px;color:#777;letter-spacing:1px}
.flogo i{display:inline-block;width:18px;height:18px;border-radius:50%;background:#2a9fe0;margin-right:6px;vertical-align:-2px}
.vline{left:863px;top:1043px;width:1px;height:140px;border-left:1px dotted #333}
</style>
</head>
<body>
<div class="page">

  <header class="abs header">
    <div class="abs brand-mark"></div>
    <div class="abs brand">47VORA</div>
    <nav class="abs nav">
      <span>Copmany</span><span class="sep">|</span>
      <span>Technical Services</span><span class="sep">|</span>
      <span>Creative Services</span><span class="sep">|</span>
      <span>Partners</span><span class="sep">|</span>
      <span>Contact Us</span>
    </nav>
  </header>

  <section class="abs hero">
    <div class="abs hero-photo" role="img" aria-label="Desk scene with an open notebook, coloured pencils and a hand sketching a 'Smart' illustration"></div>
    <div class="abs slide-box">
      <div class="abs slide-title">SMART</div>
      <p class="abs slide-text">Lorem Ipsum is simply dummy text of the printing and typesetting industry. Lorem Ipsum has been the industry's standard dummy text ever since the 1500s, when an unknown printer took a galley of type and scrambled it to make a type specimen book.</p>
      <div class="abs readmore">readmore</div>
    </div>
    <div class="abs slide-nav">
      <svg class="abs" style="left:4px;top:6px" width="40" height="40" aria-hidden="true"><rect width="40" height="40" fill="#111"/><path d="M25 10 L14 20 L25 30" stroke="#fff" stroke-width="4" fill="none"/></svg>
      <svg class="abs" style="left:231px;top:12px" width="20" height="28" aria-hidden="true"><path d="M5 4 L15 14 L5 24" stroke="#fff" stroke-width="4" fill="none"/></svg>
    </div>
  </section>

  <section class="abs content"></section>

  <h2 class="abs h2" style="left:128px;top:512px">Our <em>Clients</em></h2>
  <div class="abs rule" style="left:115px;top:542px;width:264px"></div>
  <div class="abs client-logo"><div class="abs client-name">Nirvaka</div></div>
  <p class="abs para" style="left:116px;top:720px;width:260px">Lorem Ipsum is simply dummy text of the printing and typesetting industry. Lorem Ipsum has been the industry's standard dummy text ever since the 1500s, when an unknown printer took a galley of type and scrambled it to specimen book.</p>
  <div class="abs btn" style="left:118px;top:813px;width:64px">View all</div>

  <h2 class="abs h2" style="left:429px;top:516px">Our <em>Services</em></h2>
  <div class="abs rule" style="left:424px;top:542px;width:265px"></div>
  <ul class="abs services">
    <li class="active"><span>Business and Technology solutions</span></li>
    <li><span>Application Software and Web Development</span></li>
    <li><span>Business Process Re-Design (BPR)</span></li>
    <li><span>Business/Systems Analysis and Requirement Documentation</span></li>
    <li><span>Mentoring and Training</span></li>
    <li><span>Business and Technology solutions</span></li>
    <li><span>Business and Technology solutions</span></li>
    <li><span>Vendor Management</span></li>
    <li><span>Docuvault Architecture and Implementation</span></li>
  </ul>

  <h2 class="abs h2" style="left:728px;top:516px">For <em>partners</em></h2>
  <div class="abs rule" style="left:729px;top:542px;width:270px"></div>
  <div class="abs partner-photo" role="img" aria-label="Four hands clasping each other's wrists in a teamwork grip"></div>
  <p class="abs para" style="left:834px;top:550px;width:165px">Lorem Ipsum is simply dummy text of the printing and typesetting industry. Lorem Ipsum has been the industry's standard dummy text ever since the 1500s, when an unknown</p>
  <p class="abs para" style="left:730px;top:659px;width:269px">Lorem Ipsum is simply dummy text of the printing and typesetting industry. Lorem Ipsum has been the industry's standard dummy text ever since the 1500s, when an unknown printer took a galley of type and scrambled it to make a type specimen book. It has survived not only five centuries, but alsounchanged. It was popularised in the 1960sns of Lorem Ipsum.</p>
  <div class="abs btn" style="left:934px;top:813px;width:64px">Read More</div>

  <h2 class="abs h2" style="left:115px;top:848px">For <em>graphic designers</em></h2>

  <footer class="abs footer"></footer>

  <div class="abs tiles">
    <div class="tile" style="width:215px"><h3>Print</h3><div class="line"></div><div class="art" role="img" aria-label="Billboard illustration"></div><div class="more" style="right:14px"><span>More</span><b>»</b></div></div>
    <div class="tile" style="width:213px"><h3>Logo Design</h3><div class="line"></div><div class="art" role="img" aria-label="Logo design illustration"></div><div class="more" style="right:14px"><span>More</span><b>»</b></div></div>
    <div class="tile" style="width:229px"><h3>Web Design</h3><div class="line"></div><div class="art" role="img" aria-label="Cup of brushes and pencils illustration"></div><div class="more" style="right:19px"><span>More</span><b>»</b></div></div>
    <div class="tile" style="width:228px"><h3>Illustration</h3><div class="line"></div><div class="art" role="img" aria-label="Paint pot with brushes illustration"></div><div class="more" style="right:14px"><span>More</span><b>»</b></div></div>
  </div>

  <div class="abs fcol arrows" style="left:124px;top:1038px"><h4>Quick Linka</h4>
    <ul><li>Copmany</li><li>Technical Services</li><li>Creative Services</li><li>Partners</li><li>Contact Us</li></ul></div>
  <div class="abs fcol" style="left:292px;top:1038px"><h4>Contact</h4>
    <ul style="margin-top:10px"><li style="line-height:18.6px">UK: +447700900</li><li style="line-height:18.6px">USA: +14155550</li><li style="line-height:18.6px">text@corvinsoft-example.com</li></ul></div>
  <div class="abs fcol" style="left:460px;top:1037px"><h4>Follow Us</h4>
    <ul style="margin-top:10px"><li style="line-height:18.6px"><i class="ico"></i>FRIENDSHEET</li><li style="line-height:18.6px"><i class="ico" style="background:#58c4e8"></i>CHIRPER</li><li style="line-height:18.6px"><i class="ico"></i>LINKWORK</li></ul></div>
  <div class="abs fcol arrows" style="left:666px;top:1037px"><h4>Graphic Designers</h4>
    <ul><li>Print</li><li>Logo Design</li><li>Website Design</li><li>Illustration</li></ul></div>
  <div class="abs vline"></div>
  <div class="abs flogo"><i></i>47VORA</div>

</div>
</body>
</html>
```